Private Investment Firm Needs PowerPoint Presentation Template

Design PowerPoint template, take Pinebrook-submitted rough presentation draft, and drop it into new template. See attached Project Brief file for more detail.
Updates

Some decent designs have been submitted but they seem to lack the understanding of our target markets. I am hopeful that more time and feedback will result in better results.

Target Market(s)

Private company owners and intermediaries.

Font styles to use
Serif

Colors
3176b5

Requirements
Must have
• See attached Project Brief.
Nice to have
Should not have
• No B2C fluff--this is a B2B project.

```html
<!DOCTYPE html>
<html lang="en">
<head>
<meta charset="utf-8">
<title>What We Do / And Why</title>
<link rel="stylesheet" href="https://fonts.googleapis.com/css2?family=Montserrat:wght@500;600;700&family=Tinos&display=swap">
<style>
  :root {
    --brand-blue: #1a6fc0;
    --panel-blue: rgba(18, 104, 196, 0.92);
    --photo-dark: #0c2f3a;
    --photo-mid: #1d5360;
    --ink-grey: #545454;
    --white: #ffffff;
  }
  * { margin: 0; padding: 0; box-sizing: border-box; }
  html, body { width: 1200px; height: 676px; overflow: hidden; background: var(--white); }
  .slide {
    position: relative;
    width: 1200px;
    height: 676px;
    overflow: hidden;
    background: var(--white);
    font-family: "Montserrat", Arial, sans-serif;
  }
  .side-bar {
    position: absolute; left: 0; top: 0;
    width: 44px; height: 676px;
    background: var(--brand-blue);
  }
  .side-url {
    position: absolute;
    left: 22px; top: 336px;
    transform: translate(-50%, -50%) rotate(-90deg);
    font-family: "Tinos", "Times New Roman", serif;
    font-size: 15px;
    color: var(--white);
    white-space: nowrap;
  }
  .edge-bar {
    position: absolute; right: 0; top: 0;
    width: 12px; height: 676px;
    background: var(--brand-blue);
  }
  .page-number {
    position: absolute; right: 20px; top: 18px;
    font-family: "Tinos", "Times New Roman", serif;
    font-size: 20px; color: #222;
  }
  .section-title {
    position: absolute; left: 86px; top: 82px;
    font-size: 29px; font-weight: 700;
    letter-spacing: 0.3px;
    color: var(--brand-blue);
  }
  .statement {
    position: absolute; right: 748px; top: 242px;
    text-align: right;
    font-size: 44px; font-weight: 600;
    line-height: 42px;
    color: var(--ink-grey);
  }
  .photo-band {
    position: absolute; left: 483px; top: 101px;
    width: 705px; height: 470px;
    background: linear-gradient(120deg, var(--photo-dark), var(--photo-mid) 45%, var(--photo-dark));
  }
  .reasons-panel {
    position: absolute; left: 483px; top: 170px;
    width: 705px; height: 334px;
    background: var(--panel-blue);
    padding: 20px 80px 0 61px;
  }
  .reasons { list-style: none; }
  .reasons li {
    position: relative;
    padding-left: 17px;
    color: var(--white);
    font-size: 17.5px; font-weight: 500;
    line-height: 28px;
    margin-bottom: 28px;
  }
  .reasons li svg { position: absolute; left: -2px; top: 8px; }
  .brand-mark {
    position: absolute; left: 68px; top: 620px;
    display: flex; align-items: center; gap: 10px;
  }
  .brand-name {
    font-size: 17px; font-weight: 600;
    letter-spacing: 1.5px;
    color: var(--brand-blue);
  }
</style>
</head>
<body>
<div class="slide">
  <div class="side-bar"></div>
  <div class="side-url">www.pinebrookcapital.com</div>
  <div class="edge-bar"></div>
  <div class="page-number">10</div>

  <h1 class="section-title">WHAT WE DO / AND WHY</h1>

  <p class="statement">Non-Control<br>Capital<br>transactions<br>only</p>

  <div class="photo-band" role="img" aria-label="Dark teal photograph of scattered dollar banknotes"></div>

  <div class="reasons-panel">
    <ul class="reasons">
      <li><svg width="12" height="12" viewBox="0 0 12 12"><path d="M6 1 L11 6 L6 11 L1 6 Z" fill="none" stroke="#fff" stroke-width="2.4"/></svg>Companies looking for a partner to help them grow, not sellers looking to exit</li>
      <li><svg width="12" height="12" viewBox="0 0 12 12"><path d="M6 1 L11 6 L6 11 L1 6 Z" fill="none" stroke="#fff" stroke-width="2.4"/></svg>Management’s personal wealth directly tied to the performance of the investment</li>
      <li><svg width="12" height="12" viewBox="0 0 12 12"><path d="M6 1 L11 6 L6 11 L1 6 Z" fill="none" stroke="#fff" stroke-width="2.4"/></svg>Situational investors with a generalist approach</li>
      <li><svg width="12" height="12" viewBox="0 0 12 12"><path d="M6 1 L11 6 L6 11 L1 6 Z" fill="none" stroke="#fff" stroke-width="2.4"/></svg>Our heritage reflects decades of Non-Control Capital investing—it’s all we do</li>
    </ul>
  </div>

  <div class="brand-mark">
    <svg width="30" height="30" viewBox="0 0 30 30"><circle cx="15" cy="15" r="13" fill="none" stroke="#1a6fc0" stroke-width="3"/></svg>
    <span class="brand-name">PINEBROOK CAPITAL</span>
  </div>
</div>
</body>
</html>
```